Chocolate Bar Design

I need packaging design for a new line of chocolate bars.

The new design must fit in with the packaging design for our line of solid chocolate bars. The previous bars are packaged in clear boxes, the new line is in 3x3 kraft boxes so the new design must be visusally appealing, and portray what lies inside as they are not able to view the bar itself.

The new product line is for "Truffle Bars", basically a chocolate bar with a truffle filling. The first three flavors are Velmora Ember (Cinnamon and Cayenne, Sea Salt), Cafe Mocha, and Pumpkin Pie.

These are artisan bars, and should reflect in the packaging.

If you view our previous packaging, they are the same design but with a different color for each flavor, which would be ideal.

Industry/Entity Type

Cafe

Requirements
Must have
• Each design should include the front label that has the company name, size of the bar, and name of the bar at minimum. The reverse label must have company name, address, website, and ingredients, at minimum.

Nice to have
• Ideally, I would be able to edit ingredients, and bar names easily.

```html
<!DOCTYPE html>
<html lang="en">
<head>
<meta charset="utf-8">
<title>Harlow Pierce Truffle Bar Labels</title>
<link rel="stylesheet" href="https://fonts.googleapis.com/css2?family=Libre+Baskerville:ital,wght@0,400;0,700;1,700&display=swap">
<style>
  :root {
    --gold: #c4a466;
    --paper: #ffffff;
    --ink: #2a1a10;
    --rule: #3a3a3a;

    --mocha-strip: #8e6a4e;
    --mocha-band: #6b4029;
    --mocha-mid: #9a7050;
    --mocha-photo: #7a4a30;

    --ember-strip: #b0553a;
    --ember-band: #8c2b10;
    --ember-mid: #b75c3a;
    --ember-photo: #6e3a22;

    --pumpkin-strip: #f07a3a;
    --pumpkin-band: #e84030;
    --pumpkin-mid: #f07838;
    --pumpkin-photo: #7a4a30;
  }

  * { box-sizing: border-box; margin: 0; padding: 0; }

  html, body {
    width: 1200px;
    height: 428px;
    overflow: hidden;
    background: var(--paper);
  }

  .canvas {
    position: relative;
    width: 1200px;
    height: 428px;
    font-family: "Libre Baskerville", Georgia, serif;
  }

  .label {
    position: absolute;
    top: 28px;
    width: 369px;
    height: 369px;
    background: var(--paper);
    overflow: hidden;
  }
  .label--mocha   { left: 28px;  --strip: var(--mocha-strip);   --band: var(--mocha-band);   --mid: var(--mocha-mid);   --photo: var(--mocha-photo); }
  .label--ember   { left: 415px; --strip: var(--ember-strip);   --band: var(--ember-band);   --mid: var(--ember-mid);   --photo: var(--ember-photo); }
  .label--pumpkin { left: 803px; --strip: var(--pumpkin-strip); --band: var(--pumpkin-band); --mid: var(--pumpkin-mid); --photo: var(--pumpkin-photo); }

  .label__gold {
    position: absolute;
    left: 0; right: 0;
    height: 25px;
    background: var(--gold);
  }
  .label__gold--top { top: 0; }
  .label__gold--bottom { bottom: 0; height: 29px; }

  .brand {
    position: absolute;
    top: 25px; left: 0; right: 0;
    height: 95px;
    display: flex;
    align-items: center;
    justify-content: center;
  }
  .brand__name {
    font-size: 29px;
    font-weight: 400;
    color: var(--ink);
    letter-spacing: 0.5px;
  }

  .label__strip {
    position: absolute;
    top: 120px; left: 0; right: 0;
    height: 9px;
    background: var(--strip);
  }

  .flavor {
    position: absolute;
    top: 129px; left: 0; right: 0;
    height: 75px;
    background: var(--band);
    display: flex;
    align-items: center;
    justify-content: center;
  }
  .flavor__name {
    font-size: 24px;
    font-weight: 700;
    color: var(--gold);
  }

  .tagline {
    position: absolute;
    top: 204px; left: 0; right: 0;
    height: 69px;
    background: var(--mid);
    padding: 13px 0 0 22px;
  }
  .tagline__text {
    font-size: 15px;
    font-style: italic;
    font-weight: 700;
    line-height: 21px;
    color: var(--ink);
  }

  .weight {
    position: absolute;
    top: 305px;
    left: 18px;
    font-size: 11px;
    font-weight: 400;
    color: var(--ink);
    letter-spacing: 0.2px;
  }

  .product-photo {
    position: absolute;
    left: 230px;
    top: 180px;
    width: 119px;
    height: 156px;
  }
  .product-photo rect { fill: var(--photo); }

  .baseline {
    position: absolute;
    left: 0;
    top: 416px;
    width: 1200px;
    height: 1px;
    background: var(--rule);
  }
</style>
</head>
<body>
<main class="canvas">

  <section class="label label--mocha">
    <div class="label__gold label__gold--top"></div>
    <header class="brand"><span class="brand__name">Harlow Pierce</span></header>
    <div class="label__strip"></div>
    <div class="flavor"><h2 class="flavor__name">Cafe Mocha</h2></div>
    <div class="tagline"><p class="tagline__text">Hand-made chocolate<br>bar with Truffle filling</p></div>
    <p class="weight">NET WT. 3,5 OZ / 99.2 G</p>
    <svg class="product-photo" viewBox="0 0 119 156" role="img" aria-label="Photo of a stacked milk chocolate truffle bar piece">
      <defs>
        <linearGradient id="choc-mocha" x1="0" y1="0" x2="1" y2="1">
          <stop offset="0" stop-color="#a0694a"/>
          <stop offset="1" stop-color="#5a3320"/>
        </linearGradient>
      </defs>
      <rect x="0" y="0" width="119" height="156" rx="6" style="fill:url(#choc-mocha)"/>
    </svg>
    <div class="label__gold label__gold--bottom"></div>
  </section>

  <section class="label label--ember">
    <div class="label__gold label__gold--top"></div>
    <header class="brand"><span class="brand__name">Harlow Pierce</span></header>
    <div class="label__strip"></div>
    <div class="flavor"><h2 class="flavor__name">Velmora Ember</h2></div>
    <div class="tagline"><p class="tagline__text">Hand-made chocolate<br>bar with Truffle filling</p></div>
    <p class="weight">NET WT. 3,5 OZ / 99.2 G</p>
    <svg class="product-photo" viewBox="0 0 119 156" role="img" aria-label="Photo of a stacked milk chocolate truffle bar piece">
      <defs>
        <linearGradient id="choc-ember" x1="0" y1="0" x2="1" y2="1">
          <stop offset="0" stop-color="#a0694a"/>
          <stop offset="1" stop-color="#5a3320"/>
        </linearGradient>
      </defs>
      <rect x="0" y="0" width="119" height="156" rx="6" style="fill:url(#choc-ember)"/>
    </svg>
    <div class="label__gold label__gold--bottom"></div>
  </section>

  <section class="label label--pumpkin">
    <div class="label__gold label__gold--top"></div>
    <header class="brand"><span class="brand__name">Harlow Pierce</span></header>
    <div class="label__strip"></div>
    <div class="flavor"><h2 class="flavor__name">Pumpkin Pie</h2></div>
    <div class="tagline"><p class="tagline__text">Hand-made chocolate<br>bar with Truffle filling</p></div>
    <p class="weight">NET WT. 3,5 OZ / 99.2 G</p>
    <svg class="product-photo" viewBox="0 0 119 156" role="img" aria-label="Photo of a stacked milk chocolate truffle bar piece">
      <defs>
        <linearGradient id="choc-pumpkin" x1="0" y1="0" x2="1" y2="1">
          <stop offset="0" stop-color="#a0694a"/>
          <stop offset="1" stop-color="#5a3320"/>
        </linearGradient>
      </defs>
      <rect x="0" y="0" width="119" height="156" rx="6" style="fill:url(#choc-pumpkin)"/>
    </svg>
    <div class="label__gold label__gold--bottom"></div>
  </section>

  <div class="baseline"></div>
</main>
</body>
</html>
```